Need website redesign!

I have a site, www.mapleridgefitcamp.example

I am looking to have it redesigned to make it simpler, and encourage people who hit the home page to click on a service, opt in, or contact me for more info. Having a video front and center with icons representing the services we offer around it may be a good idea, but I am open to YOUR design. Conversion is my goal. I want it to be friendly, but convey the fun and ENERGY of my bootcamp. Scrolling pics on home page so people can get a feel for our bootcamp is recommended as well.

```html
<!DOCTYPE html>
<html lang="en">
<head>
<meta charset="utf-8">
<title>Maple Ridge Fit Camp</title>
<link href="https://fonts.googleapis.com/css2?family=Raleway:wght@300;400;500;600;700;800&display=swap" rel="stylesheet">
<style>
:root{
  --red:#ed1c24;
  --navy:#141a33;
  --black:#000;
  --footer:#222;
  --text:#222;
  --muted:#555;
  --card:#eeeeee;
  --panel:#efeeeb;
  --blue:#3b5a9a;
  --social:#555b66;
  --white:#fff;
}
*{box-sizing:border-box;margin:0;padding:0}
html,body{width:696px;height:1200px;overflow:hidden;background:var(--white)}
body{position:relative;font-family:'Raleway',sans-serif;color:var(--text)}
.abs{position:absolute}

/* header */
.site-header{left:0;top:0;width:696px;height:58px;background:var(--black);border-bottom:2px solid var(--red)}
.brand{left:53px;top:0;width:65px;height:64px;background:var(--black);display:flex;align-items:center;justify-content:center;text-align:center;color:var(--red);font-weight:800;font-size:10px;line-height:1.1;z-index:3}
.main-nav{right:47px;top:25px;display:flex;gap:14px;font-size:7.4px;font-weight:700;text-transform:uppercase}
.main-nav a{color:var(--red);text-decoration:none}
.main-nav a.active{color:var(--white)}

/* hero */
.hero{left:0;top:58px;width:696px;height:238px;background:linear-gradient(100deg,#d9c7a8 0%,#c9b08e 30%,#3aa6a8 45%,#2f3440 65%,#d8d2c8 85%,#9c8a6c 100%)}
.hero-floor{left:0;top:278px;width:696px;height:18px;background:linear-gradient(90deg,#5b4aa0,#6e60b8)}
.hero-title{left:52px;top:192px;color:var(--white);font-weight:700;font-size:22.4px;line-height:28px;text-shadow:0 1px 3px rgba(0,0,0,.5);z-index:2}
.optin-card{left:458px;top:80px;width:149px;height:190px;background:rgba(255,255,255,.85)}
.optin-card .head{height:56px;background:var(--navy);border-bottom:2px solid var(--red);color:var(--white);font-weight:700;font-size:9.4px;line-height:12px;padding:10px 13px}
.optin-card label{display:block;font-size:6.6px;font-weight:500;margin:10px 0 3px 14px}
.optin-card .field{margin-left:14px;width:118px;height:18px;border:1px solid var(--red);background:var(--white);font-size:6px;color:#aaa;padding:5px 6px}
.btn{display:inline-block;font-size:6.4px;font-weight:800;text-transform:uppercase;color:var(--white);text-align:center;line-height:13px;height:13px;padding:0 10px}
.btn-dark{background:var(--navy)}
.btn-red{background:var(--red);font-weight:500;text-transform:none}
.btn-blue{background:var(--blue)}
.optin-card .btn{margin:16px 0 0 14px;height:17px;line-height:17px}

/* band */
.services-band{left:0;top:296px;width:696px;height:59px;background:var(--navy);color:var(--white);font-size:15.4px;font-weight:500;text-align:center;line-height:59px}

/* intro */
.video{left:53px;top:380px;width:196px;height:152px;background:#000}
.video .frame{position:absolute;left:55px;top:18px;width:88px;height:114px;background:linear-gradient(#6a5a3a,#3a3026)}
.video .caption{position:absolute;left:7px;top:4px;color:#fff;font-size:6.6px}
.video .bar{position:absolute;left:0;top:132px;width:196px;height:2px;background:#555}
.video .bar::before{content:"";position:absolute;left:0;top:0;width:13px;height:2px;background:var(--red)}
.video .time{position:absolute;left:58px;top:138px;color:#fff;font-size:6px}
.intro-title{left:278px;top:400px;font-size:16px;font-weight:400}
.intro-text{left:278px;top:426px;width:260px;font-size:6.4px;line-height:12.6px;color:var(--text)}
.intro-actions{left:278px;top:510px;display:flex;gap:5px}

/* services */
.rule{left:53px;top:567px;width:596px;height:1px;background:#ccc}
.section-title{left:0;top:557px;width:696px;text-align:center;font-size:16px;font-weight:400;line-height:20px}
.section-title span{background:var(--white);padding:0 14px}
.arrow-btn{top:556px;width:21px;height:21px;border-radius:50%;background:#e8e8e8}
.services{left:53px;top:605px;width:596px;display:flex;gap:3px}
.service{width:83px;height:127px;background:var(--card);text-align:center}
.service .photo{height:75px}
.service h3{font-size:9.4px;font-weight:500;line-height:11px;height:30px;display:flex;align-items:center;justify-content:center;margin-top:4px}
.service .btn{margin-top:6px;padding:0 8px}

/* opt-in strip */
.optin-strip{left:53px;top:762px;width:596px;height:100px;background:var(--panel);border-bottom:1.5px solid var(--red)}
.optin-strip h2{position:absolute;left:29px;top:17px;color:var(--red);font-size:15.6px;font-weight:700;line-height:19px}
.optin-strip label{position:absolute;top:30px;font-size:6.6px;font-weight:500}
.optin-strip .field{position:absolute;top:40px;width:118px;height:18px;border:1px solid var(--red);background:var(--white);font-size:6px;color:#aaa;padding:5px 7px}
.optin-strip .btn{position:absolute;left:489px;top:40px;height:18px;line-height:18px}

/* tagline */
.tagline{left:0;top:885px;width:696px;text-align:center;font-size:13.4px;line-height:16px;color:#333}
.tagline strong{color:var(--red);font-weight:800}

/* gallery */
.gallery{left:52px;top:967px;display:flex;gap:5px}
.gallery .thumb{width:83px;height:63px}
.gallery-cta{left:494px;top:967px;width:155px;height:63px;background:var(--red);color:var(--white);font-weight:700;font-size:13px;line-height:16px;padding:9px 14px}
.gallery-cta svg{position:absolute;right:9px;top:12px}

/* footer */
.site-footer{left:0;top:1072px;width:696px;height:104px;background:var(--footer)}
.footer-brand{left:53px;top:1060px;width:65px;height:64px;background:var(--black);display:flex;align-items:center;justify-content:center;text-align:center;color:var(--red);font-weight:800;font-size:10px;line-height:1.1}
.addresses{left:54px;top:1130px;color:#ddd;font-size:6.2px;line-height:8.6px}
.addresses p+p{margin-top:3px}
.footer-nav{left:367px;top:1090px;color:#ddd;font-size:6.6px;line-height:12.6px}
.footer-nav .dash{position:absolute;left:-19px;top:6px;width:9px;height:2px;background:var(--red)}
.locations-label{left:466px;top:1087px;color:#ddd;font-size:6.4px}
.map{left:466px;top:1098px;width:183px;height:71px;background:linear-gradient(135deg,#eceae4,#dcd9d0)}
.bottom-bar{left:0;top:1176px;width:696px;height:24px;background:var(--black);color:#ccc;font-size:6.4px}
.bottom-bar .copy{position:absolute;left:54px;top:8px}
.bottom-bar .legal{position:absolute;left:466px;top:8px}
.social{position:absolute;top:5px;width:13px;height:13px;border-radius:50%;background:var(--social)}
</style>
</head>
<body>

<header class="abs site-header"></header>
<div class="abs brand">Maple Ridge Fit Camp</div>
<nav class="abs main-nav">
  <a class="active">Home</a><a>Services</a><a>Classes</a><a>About Us</a><a>FAQ's</a><a>Contact Us</a>
</nav>

<section class="abs hero" role="img" aria-label="Smiling woman in a teal top stretching on a gym mat"></section>
<div class="abs hero-floor" role="img" aria-label="Purple exercise mat"></div>
<h1 class="abs hero-title">Morning,<br>Evening and<br>Weekend Hours!</h1>

<form class="abs optin-card">
  <div class="head">Leave your email for a FREE week of bootcamp, NO OBLIGATION</div>
  <label>Name</label><div class="field">Enter Your Name</div>
  <label>Email</label><div class="field">Enter Your Email ID</div>
  <span class="btn btn-dark">Get Started Now</span>
</form>

<div class="abs services-band">Fat Loss Bootcamps, Martial Arts, Yoga, Kids Fitness, Personal Training</div>

<div class="abs video">
  <div class="frame" role="img" aria-label="Video of a member sharing his weight loss story"></div>
  <span class="caption">Dan R lost 15 pounds in just 17 sessi...</span>
  <div class="bar"></div>
  <svg class="abs" style="left:12px;top:138px" width="8" height="8" viewBox="0 0 8 8"><path d="M1 0 L8 4 L1 8Z" fill="#ccc"/></svg>
  <span class="time">0:00 / 0:16</span>
</div>
<h2 class="abs intro-title">What is Maple Ridge Fit Camp</h2>
<p class="abs intro-text">Lorem Ipsum is simply dummy text of the printing and typesetting industry. Lorem Ipsum has been the industry's standard dummy text ever since the 1500s, when ... unknown printer took a galley of type and scrambled it to make a type specimen book.Lorem Ipsum is simply standard dummy text ever since the 1500s, when ... unknown printer took a galley of type and scrambled it to make a type specimen book.</p>
<div class="abs intro-actions">
  <span class="btn btn-red">Read More</span>
  <span class="btn btn-dark">Get Started Now</span>
  <span class="btn btn-blue">Follow Us Online</span>
</div>

<div class="abs rule"></div>
<h2 class="abs section-title"><span>Our Services</span></h2>
<svg class="abs arrow-btn" style="left:266px" viewBox="0 0 21 21"><path d="M12 6 L8 10.5 L12 15" fill="none" stroke="#aaa" stroke-width="1.4"/></svg>
<svg class="abs arrow-btn" style="left:413px" viewBox="0 0 21 21"><path d="M9 6 L13 10.5 L9 15" fill="none" stroke="#222" stroke-width="1.4"/></svg>

<div class="abs services">
  <div class="service"><div class="photo" role="img" aria-label="Group training with battle ropes" style="background:linear-gradient(#8a8f9a,#3c3c44)"></div><h3>Boot Camp</h3><span class="btn btn-red">Read More</span></div>
  <div class="service"><div class="photo" role="img" aria-label="Trainer coaching suspension strap exercise" style="background:linear-gradient(#6d6a6a,#2c3a55)"></div><h3>Personal<br>training</h3><span class="btn btn-red">Read More</span></div>
  <div class="service"><div class="photo" role="img" aria-label="Large group of young athletes" style="background:linear-gradient(#7a6a80,#4a3a58)"></div><h3>Youth Sports/<br>Agility</h3><span class="btn btn-red">Read More</span></div>
  <div class="service"><div class="photo" role="img" aria-label="Yoga instructor portrait" style="background:linear-gradient(#6a4a3a,#b23a3a)"></div><h3>Yoga</h3><span class="btn btn-red">Read More</span></div>
  <div class="service"><div class="photo" role="img" aria-label="Woman doing push-ups" style="background:linear-gradient(#d8d0c8,#a08a78)"></div><h3>Bride transform-<br>ation programs</h3><span class="btn btn-red">Read More</span></div>
  <div class="service"><div class="photo" role="img" aria-label="Black belt and birthday cake" style="background:linear-gradient(#d8d6d2,#3a3a3a)"></div><h3>Kids birthday<br>parties</h3><span class="btn btn-red">Read More</span></div>
  <div class="service"><div class="photo" role="img" aria-label="Team group photo in a gym" style="background:linear-gradient(#c8ccd2,#6a7a8a)"></div><h3>Corporate<br>Team Building</h3><span class="btn btn-red">Read More</span></div>
</div>

<form class="abs optin-strip">
  <h2>Leave your email for a<br>FREE week of bootcamp,<br>NO OBLIGATION</h2>
  <label style="left:239px">Name</label><div class="field" style="left:239px">Enter Your Name</div>
  <label style="left:365px">Email</label><div class="field" style="left:365px">Enter Your Email ID</div>
  <span class="btn btn-dark">Get Started Now</span>
</form>

<p class="abs tagline">A fun, friendly, and effective place for you to shed serious fat,<br>build tight lean muscle, and have the time of your life doing it.<br>So...what are you waiting for? Register now and try us out <strong>RISK FREE!</strong></p>

<div class="abs gallery">
  <div class="thumb" role="img" aria-label="Member doing floor crunches" style="background:linear-gradient(#c8c8c0,#5a8a4a)"></div>
  <div class="thumb" role="img" aria-label="Group outdoors in the woods" style="background:linear-gradient(#6a8a4a,#3a4a6a)"></div>
  <div class="thumb" role="img" aria-label="Suspension strap training" style="background:linear-gradient(#6a6a6a,#2c3a55)"></div>
  <div class="thumb" role="img" aria-label="Outdoor lunges on grass" style="background:linear-gradient(#e0e0d8,#5a9a3a)"></div>
  <div class="thumb" role="img" aria-label="Indoor class with medicine balls" style="background:linear-gradient(#c8ccd0,#3a8a7a)"></div>
</div>
<div class="abs gallery-cta">See Our<br>Complete<br>Photo Gallery
  <svg width="16" height="40" viewBox="0 0 16 40"><path d="M2 2 L14 20 L2 38" fill="none" stroke="#fff" stroke-width="1.2"/></svg>
</div>

<footer class="abs site-footer"></footer>
<div class="abs footer-brand">Maple Ridge Fit Camp</div>
<div class="abs addresses">
  <p>Cedar Hollow Martial Arts Studio<br>1280 Birchwood Lane, Maple Ridge, MD 20100</p>
  <p>Oakview Maple Ridge Fit Camp<br>4410 Commerce Court, Suite B, Oakview, MD 20200</p>
</div>
<nav class="abs footer-nav"><span class="dash"></span>Home<br>Services<br>Classes<br>About Us<br>Join Now<br>Contact Us</nav>
<div class="abs locations-label">Our Locations &#8964;</div>
<div class="abs map" role="img" aria-label="Street map showing the gym location">
  <svg class="abs" style="left:88px;top:30px" width="8" height="12" viewBox="0 0 8 12"><path d="M4 12 L0.8 5 A3.6 3.6 0 1 1 7.2 5Z" fill="var(--red)"/><circle cx="4" cy="4" r="1.4" fill="#fff"/></svg>
</div>
<div class="abs bottom-bar">
  <span class="copy">© 2014 Maple Ridge Fit Camp</span>
  <span class="legal">Privacy Policy &nbsp;|&nbsp; Disclaimer</span>
  <span class="social" style="left:604px"></span>
  <span class="social" style="left:620px"></span>
  <span class="social" style="left:636px"></span>
</div>

</body>
</html>
```